Stylish Business Cards Wanted

- DOUBLE SIDED Design Required -

High end, edgy cards for a corporate and personal stylist. Must include logo,
Name: Belinda Harwick
Title: Director and Stylist
telephone : +61 8 7142 5809
email: belinda@theloombriefing.example
website: theloombriefing.example
Tag: Corporate Workwear & Uniform Specialist | Personal Stylist
Would like nice icons for telephone, email, website

Target Market(s)

Businesses wanting stylish uniforms, people wanting stylish wardrobes

Industry/Entity Type

Corporate Workwear Stylist

Contact Information for Business Card

I would like black, white and gold foiling incorporated in the design - possibly a touch of the other colours on my branding guide attached Name: Belinda Harwick Title: Director and Stylist telephone : +61 8 7142 5809 email: belinda@theloombriefing.example website: theloombriefing.example Tag: Corporate Workwear & Uniform Specialist | Personal Stylist Would like nice icons for telephone, email, website

Font styles to use
Other font styles liked:
• Raleway

Colors

Designer to choose colors to be used in the design.

Requirements
Must have
• Gold foil accents

```html
<!DOCTYPE html>
<html lang="en">
<head>
<meta charset="utf-8">
<title>The Loom Briefing – Business Cards</title>
<link href="https://fonts.googleapis.com/css2?family=Dancing+Script:wght@500;600&family=Raleway:wght@600&family=Roboto:wght@400&display=swap" rel="stylesheet">
<style>
  :root {
    --backdrop: #3a3a3c;
    --card-white: #fbfbfa;
    --navy: #171d37;
    --gold: #e3b64f;
    --gold-deep: #c9962f;
    --ink: #1b1b24;
    --accent-pink: #c0306a;
  }
  * { margin: 0; padding: 0; box-sizing: border-box; }
  html, body { width: 799px; height: 1200px; overflow: hidden; }
  body {
    background: var(--backdrop);
    position: relative;
    font-family: "Roboto", Arial, sans-serif;
  }
  .card {
    position: absolute;
    left: 85px;
    width: 630px;
    height: 360px;
    border-radius: 24px;
    background: var(--card-white);
    overflow: hidden;
  }
  .card-front { top: 150px; }
  .card-back { top: 690px; }

  .front-brand {
    position: absolute;
    inset: 0;
    display: flex;
    align-items: center;
    justify-content: center;
    font-family: "Raleway", sans-serif;
    font-weight: 600;
    font-size: 46px;
    letter-spacing: 1px;
    color: var(--gold-deep);
  }

  .wave { position: absolute; inset: 0; }

  .holder-name {
    position: absolute;
    left: 38px; top: 64px;
    font-family: "Dancing Script", cursive;
    font-weight: 600;
    font-size: 34px;
    line-height: 42px;
    color: var(--gold);
  }
  .holder-title {
    position: absolute;
    left: 40px; top: 110px;
    font-size: 15px;
    color: var(--ink);
  }
  .contact-list {
    position: absolute;
    left: 40px; top: 150px;
    list-style: none;
  }
  .contact-list li {
    display: flex;
    align-items: center;
    gap: 10px;
    height: 28px;
    font-size: 16px;
    color: var(--ink);
  }
  .contact-list svg { width: 14px; height: 14px; flex: none; }
  .social-mark {
    width: 14px; height: 14px;
    background: var(--gold);
    border-radius: 3px;
    flex: none;
  }

  .tagline {
    position: absolute;
    right: 34px; top: 40px;
    text-align: right;
    font-family: "Dancing Script", cursive;
    font-weight: 500;
    font-size: 17px;
    line-height: 22px;
    color: #ffffff;
  }
  .tagline span::after {
    content: "";
    display: inline-block;
    width: 0; height: 0;
    margin-left: 8px;
    border-left: 5px solid var(--accent-pink);
    border-top: 3px solid transparent;
    border-bottom: 3px solid transparent;
    vertical-align: middle;
  }

  .back-brand {
    position: absolute;
    right: 36px; bottom: 44px;
    display: flex;
    align-items: center;
    gap: 10px;
    font-family: "Raleway", sans-serif;
    font-weight: 600;
    font-size: 28px;
    color: var(--navy);
  }
  .back-brand .brand-square {
    width: 14px; height: 14px;
    background: var(--gold);
  }
</style>
</head>
<body>
  <section class="card card-front">
    <div class="front-brand">The Loom Briefing</div>
  </section>

  <section class="card card-back">
    <svg class="wave" viewBox="0 0 630 360" aria-hidden="true">
      <defs>
        <linearGradient id="foil" x1="0" y1="0" x2="1" y2="0">
          <stop offset="0" stop-color="#c9962f"/>
          <stop offset="0.5" stop-color="#f2cd6b"/>
          <stop offset="1" stop-color="#d6a640"/>
        </linearGradient>
      </defs>
      <path d="M0,0 H630 V236 C550,236 500,180 460,120 C400,30 260,10 0,8 Z" fill="var(--navy)"/>
      <path d="M0,24 C260,26 380,40 440,110 C490,175 550,245 630,248" fill="none" stroke="url(#foil)" stroke-width="6"/>
      <path d="M150,15 C250,18 330,30 390,62" fill="none" stroke="url(#foil)" stroke-width="2.5"/>
    </svg>

    <h1 class="holder-name">Belinda Harwick</h1>
    <p class="holder-title">Director and Stylist</p>

    <ul class="contact-list">
      <li><span class="social-mark"></span>/theloombriefing101</li>
      <li>
        <svg viewBox="0 0 24 24"><path fill="var(--gold)" d="M6.6 10.8a15.1 15.1 0 0 0 6.6 6.6l2.2-2.2c.3-.3.7-.4 1-.2 1.1.4 2.3.6 3.6.6.6 0 1 .4 1 1V20c0 .6-.4 1-1 1A17 17 0 0 1 3 4c0-.6.4-1 1-1h3.5c.6 0 1 .4 1 1 0 1.3.2 2.5.6 3.6.1.3 0 .7-.2 1z"/></svg>
        +61 8 7142 5809
      </li>
      <li>
        <svg viewBox="0 0 24 24"><rect x="2" y="5" width="20" height="14" rx="2" fill="none" stroke="var(--gold)" stroke-width="2"/><path d="M3 6l9 7 9-7" fill="none" stroke="var(--gold)" stroke-width="2"/></svg>
        belinda@theloombriefing.example
      </li>
      <li>
        <svg viewBox="0 0 24 24"><circle cx="12" cy="12" r="10" fill="var(--gold)"/><path d="M2 12h20M12 2c3 3 3 17 0 20M12 2c-3 3-3 17 0 20" fill="none" stroke="#fff" stroke-width="1.5"/></svg>
        theloombriefing.example
      </li>
    </ul>

    <p class="tagline">
      <span>Corporate Workwear</span><br>
      <span>and Uniform Specialist</span><br>
      <span>Personal Stylist</span>
    </p>

    <div class="back-brand"><span class="brand-square"></span>The Loom Briefing</div>
  </section>
</body>
</html>
```